Verpackungsdesign für Wellness- und Saunaprodukte
Zielgruppe
BaFinn ist ein junges Start-Up, das sich auf Wellness- und Saunaprodukte spezialisiert hat. Unsere Zielgruppe besteht zu beinahe gleichen Teilen aus männlichen und weiblichen Personen zwischen 30 und 60 Jahren. Unsere Produkte befinden sich eher im mittel- bis höherpreisigen Segment, daher streben wir ein hochwertiges Design für unsere Verpackungen an. Unsere Produktpalette reicht von Mentholkristallen, Saunaaufgüssen, bis hin zu Textilien für den Wellnessbereich und soll dementsprechend Menschen ansprechen, die sich einen gewissen Luxus im Alltag auch gönnen.
Aufgabenstellung
Inspiriert von der skandinavischen Sauna Kultur, möchten wir Momente der Erholung und
Entspannung in den Alltag unserer Kunden bringen. Die Geschichte des Saunierens ist eng mit der skandinavischen Kultur verbunden und skandinavische Stilelemente sind zeitgemäß und sprechen ein breites Publikum an. Das Design muss auf Dosen/Tiegel , Karton Verpackungen und Flaschen verschiedener Größen adaptierbar sein (siehe Bild im Anhang).
40g Tiegel(transparent) Höhe 40mm Durchmesser 60mm (ohne Deckel Silber gebürstet)
100g Tiegel(transparent) Höhe 53mm Durchmesser 71mm (ohne Deckel Silber gebürstet)
200g Tiegel(transparent) Höhe 65mm Durchmesser 90mm (ohne Deckel Silber gebürstet)
Karton Verpackung 124,5x49x49mm
Karton Verpackung 100x100x100mm
Flaschenetikett 134x67mm (Braunglas, schwarzer Deckel)
Es soll ein passendes Keyvisual erstellt werden.
Im Anhang sieht man die Verpackungen, Dosen, Flaschen sowie unsere ersten Design Entwürfe (an diese Anordnung der Elemente kann sich der Designer orientieren ). Das Logo bleibt wie gegeben. Das Produkt für die Tiegel soll Mentholkristalle sein.

```html
<!DOCTYPE html>
<html lang="de">
<head>
<meta charset="utf-8">
<title>BaFinn – Verpackungsetiketten</title>
<link rel="stylesheet" href="https://fonts.googleapis.com/css2?family=Archivo+Black&family=Archivo:wght@500;600&display=swap">
<style>
  :root{
    --bg:#e6e6e6;
    --ink:#2a2b24;
    --white:#ffffff;
    --olive:#a2aa66;
    --teal:#5e9a8c;
    --berry:#b4443e;
    --spruce-dark:#2f5523;
    --spruce-light:#6f9a3e;
    --mint-dark:#1f4632;
    --mint-light:#4f7f55;
    --seed-dark:#6e1016;
    --seed-light:#c3343c;
    --logo-dot:#1c1c1c;
  }
  *{box-sizing:border-box;margin:0;padding:0}
  html,body{width:1200px;height:603px;overflow:hidden}
  body{background:var(--bg);position:relative;font-family:"Archivo",sans-serif;color:var(--ink)}

  .label{position:absolute;overflow:hidden}
  .photo{position:absolute;inset:0}
  .photo--spruce{background:radial-gradient(circle at 30% 30%,var(--spruce-light),var(--spruce-dark) 75%)}
  .photo--mint{background:linear-gradient(135deg,var(--mint-light),var(--mint-dark))}
  .photo--seeds{background:radial-gradient(circle at 50% 40%,var(--seed-light),var(--seed-dark) 85%)}

  .brand{display:flex;align-items:center;justify-content:center;gap:4px;
    font-family:"Archivo",sans-serif;font-weight:600;font-size:8px;color:var(--ink)}
  .brand__dot{width:8px;height:8px;border-radius:50%;background:var(--logo-dot)}
  .brand--light{color:var(--white)}

  .title{font-family:"Archivo Black",sans-serif;text-transform:uppercase;text-align:center;line-height:1.25;letter-spacing:.06em;color:var(--ink)}
  .sub{font-family:"Archivo",sans-serif;font-weight:500;text-transform:uppercase;text-align:center;letter-spacing:.1em;line-height:1.4}

  /* Faltschachtel */
  .carton{left:170px;top:162px;width:126px;height:324px}
  .carton .panel{position:absolute;left:11%;width:78%;top:20%;bottom:0;background:var(--olive);
    display:flex;flex-direction:column;align-items:center;padding-top:10px}
  .carton .title{font-size:14px;margin-top:82px}
  .carton .sub{font-size:7.5px;margin-top:auto;margin-bottom:30px}

  /* Flaschenetikett */
  .bottle{left:318px;top:306px;width:104px;height:178px}
  .bottle .panel{position:absolute;left:12%;width:76%;top:14%;bottom:0;background:var(--olive);
    display:flex;flex-direction:column;align-items:center;padding-top:8px}
  .bottle .title{font-size:11.5px;margin-top:24px}
  .bottle .sub{font-size:6.5px;margin-top:auto;margin-bottom:16px}

  /* Tiegeletiketten */
  .jar{top:386px;width:220px;height:90px}
  .jar--menthol{left:462px}
  .jar--peeling{left:706px}
  .jar .band{position:absolute;left:0;right:0;top:40%;bottom:0;
    display:flex;flex-direction:column;align-items:center;padding-top:6px}
  .jar--menthol .band{background:var(--teal)}
  .jar--peeling .band{background:var(--berry)}
  .jar .title{font-size:12.5px;margin-top:6px}
  .jar .sub{font-size:7px;margin-top:2px}
  .jar--peeling .title,.jar--peeling .sub{color:var(--white)}
  .jar--menthol .sub{color:var(--white)}
</style>
</head>
<body>
  <section class="label carton">
    <div class="photo photo--spruce" role="img" aria-label="Foto: frische Fichtenzweige"></div>
    <div class="panel">
      <div class="brand"><span class="brand__dot"></span>BaFinn</div>
      <h2 class="title">Nordische<br>Fichte</h2>
      <p class="sub">Aufguss<br>für die Sauna</p>
    </div>
  </section>

  <section class="label bottle">
    <div class="photo photo--spruce" role="img" aria-label="Foto: frische Fichtenzweige"></div>
    <div class="panel">
      <div class="brand"><span class="brand__dot"></span>BaFinn</div>
      <h2 class="title">Nordische<br>Fichte</h2>
      <p class="sub">Aufguss<br>für die Sauna</p>
    </div>
  </section>

  <section class="label jar jar--menthol">
    <div class="photo photo--mint" role="img" aria-label="Foto: Minzblätter"></div>
    <div class="band">
      <div class="brand brand--light"><span class="brand__dot"></span>BaFinn</div>
      <h2 class="title">Mentholkristalle</h2>
      <p class="sub">Für die Sauna</p>
    </div>
  </section>

  <section class="label jar jar--peeling">
    <div class="photo photo--seeds" role="img" aria-label="Foto: Granatapfelkerne"></div>
    <div class="band">
      <div class="brand brand--light"><span class="brand__dot"></span>BaFinn</div>
      <h2 class="title">Granatapfel-Peeling</h2>
      <p class="sub">Meersalz für den Körper</p>
    </div>
  </section>
</body>
</html>
```